Maple Roster Business Card for recruitment company

We are looking for a Business Card Design that incorporates our personal details and our busines name and logo. We are a specialized search consultancy that recruit Property and Construction professionals.
We would like a business card that stands out and is appealing to the Construction and Property industry as well.

Target Market(s)

people in the construction and property industry

Contact Information for Business Card

Business Name and logo

Font styles to use
Serif

Colors
0094D4
00A9DD
6FCCEA
C7EBF8
E9F6FB

Requirements
Must have
• Business name and logo as well as contact details
Should not have
• No photos of us please

```html
<!DOCTYPE html>
<html lang="en">
<head>
<meta charset="utf-8">
<title>Maple Roster — Business Card</title>
<link rel="stylesheet" href="https://fonts.googleapis.com/css2?family=Lora:wght@400;600;700&family=Questrial&display=swap">
<style>
  :root {
    --backdrop: #2a2c2e;
    --card-white: #f6f7f8;
    --card-white-shade: #eceef0;
    --paper: #ffffff;
    --navy: #0b3a52;
    --navy-deep: #072c40;
    --navy-light: #0d4660;
    --slate: #2f3d42;
    --ink: #3a3a3a;
    --blue-strong: #0094d4;
    --blue-bright: #00a9dd;
    --blue-soft: #6fccea;
    --blue-pale: #c7ebf8;
    --blue-mist: #e9f6fb;
  }
  html, body {
    margin: 0;
    padding: 0;
    width: 1200px;
    height: 732px;
    overflow: hidden;
    background: var(--backdrop);
  }
  .canvas {
    position: relative;
    width: 1200px;
    height: 732px;
  }
  .card {
    position: absolute;
    top: 242px;
    width: 436px;
    height: 248px;
    box-shadow: 0 6px 14px rgba(0,0,0,0.45);
    overflow: hidden;
  }
  .card--front {
    left: 144px;
    background: linear-gradient(135deg, var(--paper) 0%, var(--card-white) 55%, var(--card-white-shade) 100%);
  }
  .card--back {
    left: 621px;
    background: linear-gradient(135deg, var(--navy-light) 0%, var(--navy) 50%, var(--navy-deep) 100%);
  }

  /* Front: person */
  .person {
    position: absolute;
    left: 196px;
    top: 35px;
  }
  .person__name {
    margin: 0;
    font-family: "Lora", serif;
    font-weight: 700;
    font-size: 17px;
    line-height: 20px;
    color: var(--navy);
  }
  .person__role {
    margin: 1px 0 0;
    font-family: "Questrial", sans-serif;
    font-size: 12.5px;
    line-height: 15px;
    color: var(--ink);
    letter-spacing: 0.3px;
  }
  .contact {
    position: absolute;
    left: 196px;
    top: 90px;
    margin: 0;
    padding: 0;
    list-style: none;
    font-family: "Questrial", sans-serif;
    font-size: 12.5px;
    line-height: 14.5px;
    color: var(--ink);
    letter-spacing: 0.3px;
  }
  .contact__label {
    display: inline-block;
    width: 20px;
    font-weight: 700;
    color: var(--blue-strong);
  }

  /* Front: location */
  .location__marker {
    position: absolute;
    left: 141px;
    top: 148px;
    width: 44px;
    height: 27px;
    background: var(--slate);
    clip-path: polygon(4px 0, 44px 0, 40px 27px, 0 27px);
  }
  .location__marker svg {
    position: absolute;
    left: 16px;
    top: 5px;
  }
  .location__text {
    position: absolute;
    left: 196px;
    top: 155px;
    margin: 0;
    font-family: "Questrial", sans-serif;
    font-size: 12.5px;
    line-height: 15px;
    color: var(--ink);
    letter-spacing: 0.4px;
  }

  /* Brand lockup */
  .brand-band {
    position: absolute;
    left: 172px;
    top: 175px;
    width: 264px;
    height: 50px;
    background: var(--navy);
    clip-path: polygon(8px 0, 264px 0, 264px 50px, 0 50px);
  }
  .brand {
    display: flex;
    align-items: center;
    gap: 8px;
    white-space: nowrap;
  }
  .brand__dot {
    flex: none;
    border-radius: 50%;
    background: var(--blue-soft);
  }
  .brand__name {
    margin: 0;
    font-family: "Lora", serif;
    font-weight: 400;
    color: var(--paper);
    letter-spacing: 1.5px;
  }
  .brand-band .brand {
    position: absolute;
    left: 20px;
    top: 0;
    height: 50px;
  }
  .brand-band .brand__dot {
    width: 12px;
    height: 12px;
  }
  .brand-band .brand__name {
    font-size: 25px;
    line-height: 30px;
  }

  /* Back */
  .back__mark-area {
    position: absolute;
    left: 92px;
    top: 0;
    width: 248px;
    height: 248px;
    border-radius: 50%;
    background: radial-gradient(circle, rgba(111,204,234,0.10) 0%, rgba(111,204,234,0.05) 60%, rgba(111,204,234,0) 72%);
  }
  .card--back .brand {
    position: absolute;
    left: 0;
    right: 0;
    top: 106px;
    justify-content: center;
  }
  .card--back .brand__dot {
    width: 13px;
    height: 13px;
  }
  .card--back .brand__name {
    font-size: 27px;
    line-height: 36px;
  }
</style>
</head>
<body>
<main class="canvas">
  <section class="card card--front" aria-label="Business card front">
    <div class="person">
      <h1 class="person__name">Claire Hudson</h1>
      <p class="person__role">Director&nbsp; |&nbsp; Senior Search Consultant</p>
    </div>
    <ul class="contact">
      <li><span class="contact__label">T:</span> +64 21 555 0142</li>
      <li><span class="contact__label">E:</span> claire@mapleroster.nz</li>
      <li><span class="contact__label">W:</span> www.mapleroster.nz</li>
    </ul>
    <div class="location__marker">
      <svg width="12" height="17" viewBox="0 0 12 17" aria-hidden="true">
        <path d="M6 0C2.7 0 0 2.6 0 5.9 0 10.3 6 17 6 17s6-6.7 6-11.1C12 2.6 9.3 0 6 0z" fill="#ffffff"/>
        <circle cx="6" cy="5.9" r="2.2" fill="#2f3d42"/>
      </svg>
    </div>
    <p class="location__text">Auckland, New Zealand</p>
    <div class="brand-band">
      <div class="brand">
        <span class="brand__dot" aria-hidden="true"></span>
        <p class="brand__name">MAPLE ROSTER</p>
      </div>
    </div>
  </section>

  <section class="card card--back" aria-label="Business card back">
    <div class="back__mark-area" role="img" aria-label="Faint brand mark area"></div>
    <div class="brand">
      <span class="brand__dot" aria-hidden="true"></span>
      <p class="brand__name">MAPLE ROSTER</p>
    </div>
  </section>
</main>
</body>
</html>
```